Copper lark buildworks

Copper lark buildworks is a small construction company.
Who is a licenced builder, Carpenter, joiner,
working on heritage ,new build, speacial projects and sometimes furniture

Industry/Entity Type

Construction

```html
<!DOCTYPE html>
<html lang="en">
<head>
<meta charset="utf-8">
<title>Copper lark buildworks – business card</title>
<link href="https://fonts.googleapis.com/css2?family=Montserrat:wght@400;600;700;800&display=swap" rel="stylesheet">
<style>
  :root{
    --green:#3a8a12;
    --green-dark:#2f7510;
    --ink:#2b2b2b;
    --card:#f7f7f5;
    --backdrop:#e4e4e1;
    --white:#ffffff;
  }
  *{margin:0;padding:0;box-sizing:border-box}
  html,body{width:1200px;height:1000px;overflow:hidden}
  body{
    background:var(--backdrop);
    font-family:"Montserrat",Arial,sans-serif;
    color:var(--ink);
    position:relative;
  }
  .card{
    position:absolute;
    left:150px;top:240px;
    width:900px;height:520px;
    background:var(--card);
    border-radius:34px;
    overflow:hidden;
    box-shadow:0 10px 30px rgba(0,0,0,.18);
  }
  .brand{
    position:absolute;
    right:60px;top:52px;
    display:flex;align-items:center;gap:14px;
    font-weight:800;
    font-size:38px;
    letter-spacing:-.5px;
    color:var(--green);
  }
  .brand-mark{
    width:22px;height:22px;background:var(--green);
  }
  .person{
    position:absolute;left:78px;top:232px;
  }
  .person-name{
    font-weight:700;font-size:32px;color:var(--green);line-height:1.1;
  }
  .person-role{
    font-weight:400;font-size:19px;color:var(--ink);margin-top:4px;
  }
  .edge-tab{
    position:absolute;left:0;top:262px;
    width:44px;height:42px;background:var(--green);
  }
  .address{
    position:absolute;left:150px;top:340px;
    font-size:24px;line-height:1.35;font-weight:400;
  }
  .contact{
    position:absolute;right:60px;top:258px;
    list-style:none;
    font-size:20px;line-height:1;
  }
  .contact li{
    display:flex;align-items:center;gap:12px;margin-bottom:10px;
  }
  .contact svg{width:22px;height:22px;flex:none}
  .band{
    position:absolute;left:0;bottom:0;
    width:100%;height:94px;
    background:var(--green);
    display:flex;align-items:center;justify-content:flex-end;
    padding-right:60px;
    color:var(--white);
    font-size:22px;font-weight:400;
  }
  .band strong{font-weight:700}
</style>
</head>
<body>
  <article class="card">
    <div class="brand"><span class="brand-mark"></span>Copper lark buildworks</div>

    <span class="edge-tab"></span>
    <div class="person">
      <div class="person-name">Tomas Reyes</div>
      <div class="person-role">Licenced Builder &amp; Carpenter</div>
    </div>

    <address class="address" style="font-style:normal">
      Your Street Address Here<br>Singapore 56789
    </address>

    <ul class="contact">
      <li>
        <svg viewBox="0 0 24 24" aria-hidden="true"><circle cx="12" cy="12" r="12" fill="var(--green)"/><path d="M6 10c0-2 2-3 6-3s6 1 6 3v1h-3v-1.5h-6V11H6z M8 12h8l1 5H7z" fill="#fff"/></svg>
        0431207765
      </li>
      <li>
        <svg viewBox="0 0 24 24" aria-hidden="true"><circle cx="12" cy="12" r="12" fill="var(--green)"/><rect x="6" y="8" width="12" height="8" rx="1" fill="#fff"/><path d="M6.5 8.5 12 12.5l5.5-4" stroke="var(--green)" stroke-width="1.3" fill="none"/></svg>
        tomas@copperlark.com
      </li>
      <li>
        <svg viewBox="0 0 24 24" aria-hidden="true"><circle cx="12" cy="12" r="12" fill="var(--green)"/><circle cx="12" cy="12" r="6" stroke="#fff" stroke-width="1.3" fill="none"/><path d="M6 12h12M12 6c-3 3-3 9 0 12M12 6c3 3 3 9 0 12" stroke="#fff" stroke-width="1.1" fill="none"/></svg>
        www.copperlark.com
      </li>
    </ul>

    <div class="band">
      <p>working on <strong>heritage, new build, speacial projects, and furniture</strong></p>
    </div>
  </article>
</body>
</html>
```